Dietitian needs awesome business card

I need a contemporary design that's eye catching but professional.
My card is to given to doctors, specialists and patients alike.
I manage patients with chronic diseases
I have uploaded my logo and current business card, I would also like the other Certified Clinical Nutritionist logo incorporated into the design

Target Market(s)

Doctors, specialists and patients

Industry/Entity Type

Healthcare

Contact Information for Business Card

www.brightfieldnutrition.com.au
Ph: 0427 561 903
Fax: 6457 2183
email: marcus.k.diet@fernmail.com
Space on the back of the card with: Appointment date, Appointment time and appointment location

Font styles to use
Serif

Colors
fbee3e
876aae
ffc214

Requirements
Must have
• My Logo
• Certified Clinical Nutritionist Logo
• My 4 locations - Pinebrook Medical Centre, North Corrin Health, Hollis Medical, Ashcombe Doctors Surgery
Nice to have
• I like the colours in my current business card

```html
<!DOCTYPE html>
<html lang="en">
<head>
<meta charset="utf-8">
<title>Marcus Kellaway – Business and Appointment Cards</title>
<link href="https://fonts.googleapis.com/css2?family=Roboto+Slab:wght@400;500;700&family=Open+Sans:wght@400;600&display=swap" rel="stylesheet">
<style>
  :root {
    --navy: #1f4a7c;
    --royal: #0b4f9c;
    --lime: #8cc63f;
    --orange: #f07b22;
    --white: #ffffff;
    --grey: #b9c3d0;
    --backdrop: #ece8e2;
  }
  * { box-sizing: border-box; margin: 0; padding: 0; }
  html, body { width: 1200px; height: 913px; overflow: hidden; }
  body {
    background: var(--backdrop);
    font-family: "Roboto Slab", Georgia, serif;
    position: relative;
  }
  .card {
    position: absolute;
    width: 540px;
    height: 330px;
    background: var(--white);
    overflow: hidden;
    box-shadow: 0 6px 18px rgba(0,0,0,.18);
  }

  /* Appointment card */
  .appointment-card { left: 50px; top: 60px; }
  .appointment-title {
    position: absolute; left: 34px; top: 26px;
    color: var(--royal); font-weight: 700; font-size: 30px; letter-spacing: 1px;
  }
  .appointment-fields {
    position: absolute; left: 34px; top: 86px; right: 34px;
    display: grid; grid-template-columns: 1fr 1fr 1fr; column-gap: 26px;
  }
  .field-label { color: var(--royal); font-size: 14px; margin-bottom: 4px; }
  .field-line { height: 2px; background: var(--royal); margin-top: 30px; }
  .field-line:first-of-type { margin-top: 18px; }
  .appointment-stripe {
    position: absolute; left: 0; right: 0; top: 248px; height: 5px; background: var(--lime);
  }
  .appointment-band {
    position: absolute; left: 0; right: 0; top: 253px; bottom: 0; background: var(--royal);
    color: var(--white); font-size: 17px; line-height: 1.3; text-align: center;
    display: flex; align-items: center; justify-content: center;
  }

  /* Business card */
  .business-card { left: 610px; top: 523px; }
  .business-panel {
    position: absolute; left: 0; top: 0; bottom: 0; width: 305px; background: var(--navy);
  }
  .holder-name {
    position: absolute; left: 28px; top: 56px; font-size: 26px; color: var(--white); font-weight: 500;
  }
  .holder-name .surname { color: var(--lime); }
  .holder-role {
    position: absolute; left: 28px; top: 94px; font-size: 11px; color: var(--grey);
  }
  .contact-box {
    position: absolute; left: 150px; top: 160px; width: 300px; height: 150px;
    background: var(--navy); border-radius: 26px;
  }
  .contact-frame {
    position: absolute; left: 14px; top: 14px; right: 14px; bottom: 14px;
    border: 3px solid var(--white); border-radius: 20px;
  }
  .contact-list {
    list-style: none; position: absolute; left: 22px; top: 28px;
    color: var(--white); font-size: 13px; line-height: 22px;
  }
  .contact-list li { display: flex; align-items: center; gap: 8px; }
  .contact-list svg { width: 15px; height: 15px; flex: none; }
  .brand {
    position: absolute; left: 340px; top: 48px; display: flex; align-items: center; gap: 10px;
  }
  .brand-dot { width: 34px; height: 34px; border-radius: 50%; background: var(--lime); flex: none; }
  .brand-name { color: var(--royal); font-size: 15px; font-weight: 500; line-height: 1.2; }
  .accreditation-badge {
    position: absolute; left: 368px; top: 118px; width: 140px; height: 52px;
    background: var(--orange);
  }
</style>
</head>
<body>

  <section class="card appointment-card">
    <h2 class="appointment-title">APPOINTMENTS</h2>
    <div class="appointment-fields">
      <div class="field"><p class="field-label">date</p><div class="field-line"></div><div class="field-line"></div><div class="field-line"></div><div class="field-line"></div></div>
      <div class="field"><p class="field-label">time</p><div class="field-line"></div><div class="field-line"></div><div class="field-line"></div><div class="field-line"></div></div>
      <div class="field"><p class="field-label">location</p><div class="field-line"></div><div class="field-line"></div><div class="field-line"></div><div class="field-line"></div></div>
    </div>
    <div class="appointment-stripe"></div>
    <p class="appointment-band">If you are unable to make your appointment,<br>please call us to reschedule</p>
  </section>

  <section class="card business-card">
    <div class="business-panel"></div>
    <h1 class="holder-name">Marcus <span class="surname">KELLAWAY</span></h1>
    <p class="holder-role">Certified Clinical Nutritionist, Nutritionist and Chef</p>

    <div class="brand">
      <span class="brand-dot"></span>
      <span class="brand-name">Brightfield<br>Nutrition &amp; Dietetics</span>
    </div>
    <div class="accreditation-badge" role="img" aria-label="Accreditation badge"></div>

    <div class="contact-box">
      <div class="contact-frame"></div>
      <ul class="contact-list">
        <li><svg viewBox="0 0 16 16"><circle cx="8" cy="8" r="8" fill="#8cc63f"/><rect x="4" y="5" width="8" height="6" fill="none" stroke="#1f4a7c" stroke-width="1.2"/><path d="M4 5l4 3.5L12 5" fill="none" stroke="#1f4a7c" stroke-width="1.2"/></svg>marcus.k.diet@fernmail.com</li>
        <li><svg viewBox="0 0 16 16"><circle cx="8" cy="8" r="8" fill="#8cc63f"/><circle cx="8" cy="8" r="4.5" fill="none" stroke="#1f4a7c" stroke-width="1.2"/><path d="M3.5 8h9M8 3.5c-2 2.5-2 6.5 0 9M8 3.5c2 2.5 2 6.5 0 9" fill="none" stroke="#1f4a7c" stroke-width="1"/></svg>www.brightfieldnutrition.com.au</li>
        <li><svg viewBox="0 0 16 16"><circle cx="8" cy="8" r="8" fill="#8cc63f"/><path d="M5 4.5l2 0 .8 2-1.2 1c.6 1.2 1.4 2 2.6 2.6l1-1.2 2 .8v2c-4 .5-7.5-3-7.2-7.2z" fill="#1f4a7c"/></svg>0427 561 903</li>
        <li><svg viewBox="0 0 16 16"><circle cx="8" cy="8" r="8" fill="#8cc63f"/><rect x="5" y="4" width="6" height="3" fill="#1f4a7c"/><rect x="4" y="7" width="8" height="5" fill="#1f4a7c"/></svg>6457 2183</li>
      </ul>
    </div>
  </section>

</body>
</html>
```